Zelvo Stationary

Design the stationary of Zelvo Promotions Group.

Zelvo is a BTL company, BTL meaning "below the line". In other words Zelvo is a Promotional Marketing company (the company that design the brands promotional activities).

The design should transmit creativity, agility, boldness.

I need:
* Bis Card
* Letter head
* Envelopes, both vertical and horizontal (for legal size), and letter envelope
* Folders
* PPT template (Title page and regular page)
* CD slip (CD envelope)
* ID card (employee card)

And what ever else you want to throw in.
Updates

Guys,

Something I missed from the brief.   The predominat color should be RED.

Also, have fun and play with the exclamation mark (!) of the logo. 

Hi guys, more comments:

Remember that Zelvo is a "creativity" agency, not in the advertising side but on the promotional side, and that should reflect on the stationary.

 I want a bold design.  Bold and yet crisp.

 

Guys, i just uploaded the Logo in AI format.

I Also uploaded the actual Zelvo Bis Card, wich I like.  So I will like to see some designs with that bis card approach.

Guys, I am so sorry, but I notice in your last post that I upladed a wrong design ("13154_promotions_group_zelvo_brief225630.ai").  The problem was that I asked the designer the file in AI format and he send me thw wrong file, and since I dont have Illustrator I could not verify it.

The differences are minor, I just already ask him the correct one (similar to the EPS file).

Sorry                                   

Just post the correct AI file : "Zelvo Logo.ai"

Reason: I'm expecting more designs to choose from and also I wont be available tomorrow to decide.

Reason: Sorry guys, but we are not there yet!

Target Market(s)

Marketing directors, Marketing Managers

Industry/Entity Type

Legal

Requirements
Must have
• Must work with the logo attached.
The predominat color should be RED.
Play and have fun with the exclamation mark (!).
Should not have
• * No old fonts

Should not be:
* boring
* Informal
* rigid

```html
<!DOCTYPE html>
<html lang="es">
<head>
<meta charset="utf-8">
<title>Zelvo Promotions Group — Papelería</title>
<link href="https://fonts.googleapis.com/css2?family=Roboto:wght@400;900&display=swap" rel="stylesheet">
<style>
  :root {
    --red: #d0181f;
    --red-dark: #a80f16;
    --red-fold: #bb141b;
    --ink: #111111;
    --paper: #ffffff;
    --ring: #f6d3cc;
    --ring-text: #f0c4bb;
    --shadow: rgba(0,0,0,0.18);
    --window: #ececec;
    --window-line: #9a9a9a;
  }
  * { box-sizing: border-box; margin: 0; padding: 0; }
  html, body { width: 1200px; height: 900px; overflow: hidden; background: var(--paper); }
  body { position: relative; font-family: "Roboto", Arial, sans-serif; color: var(--ink); }

  .sheet { position: absolute; background: var(--paper); box-shadow: 2px 3px 6px var(--shadow); overflow: hidden; }

  .wordmark { position: absolute; font-weight: 900; line-height: 1; color: var(--ink); }
  .wordmark .name { display: block; letter-spacing: -1px; }
  .wordmark .tag { display: block; letter-spacing: 2px; text-transform: uppercase; }

  .address { position: absolute; font-size: 7px; line-height: 1.35; color: #333; }

  .ring { position: absolute; border-radius: 50%; border-style: solid; border-color: var(--ring); display: flex; align-items: center; justify-content: center; }
  .ring .ring-name { font-weight: 900; color: var(--ring-text); letter-spacing: -0.5px; }

  /* Horizontal envelope */
  .envelope-wide { left: 40px; top: 30px; width: 440px; height: 202px; }
  .envelope-wide .wordmark { left: 310px; top: 22px; }
  .envelope-wide .wordmark .name { font-size: 26px; }
  .envelope-wide .wordmark .tag { font-size: 6px; }
  .envelope-wide .address { left: 310px; top: 60px; }

  /* Vertical envelope */
  .envelope-tall { left: 40px; top: 256px; width: 444px; height: 624px; }
  .envelope-tall .wordmark { left: 30px; top: 36px; }
  .envelope-tall .wordmark .name { font-size: 30px; }
  .envelope-tall .wordmark .tag { font-size: 6.5px; }
  .envelope-tall .address { left: 30px; top: 88px; }
  .envelope-tall .window { position: absolute; left: 190px; top: 204px; width: 174px; height: 94px; top: 460px; left: 192px; background: var(--window); border: 1px solid var(--window-line); border-radius: 10px; }

  /* Red folder */
  .folder-red { left: 534px; top: 16px; width: 646px; height: 428px; background: var(--red); border-bottom-right-radius: 100px; }
  .folder-red .fold { position: absolute; left: 306px; top: 0; width: 1px; height: 100%; background: var(--red-dark); }
  .folder-red .url { position: absolute; left: 440px; top: 38px; font-size: 9px; color: var(--red-dark); }
  .folder-red .wordmark { left: 440px; top: 52px; color: var(--red-dark); }
  .folder-red .wordmark .name { font-size: 40px; }
  .folder-red .wordmark .tag { font-size: 9px; }
  .folder-red .address { left: 86px; top: 368px; color: var(--red-dark); }

  /* White folder */
  .folder-white { left: 540px; top: 470px; width: 654px; height: 414px; border-bottom-right-radius: 60px; }
  .folder-white .fold { position: absolute; left: 300px; top: 0; width: 1px; height: 100%; background: #d8d8d8; }
  .folder-white .wordmark { left: 400px; top: 28px; text-align: left; }
  .folder-white .wordmark .name { font-size: 44px; }
  .folder-white .wordmark .tag { font-size: 9.5px; }
  .folder-white .url { position: absolute; left: 484px; top: 88px; font-size: 10px; color: var(--red); }
  .folder-white .hero { position: absolute; left: 22px; top: 40px; display: flex; align-items: center; gap: 14px; }
  .folder-white .hero-dot { width: 70px; height: 70px; border-radius: 50%; background: var(--red); }
  .folder-white .hero-name { font-weight: 900; font-size: 82px; color: var(--ink); letter-spacing: -2px; line-height: 1; }
  .folder-white .address { left: 26px; top: 350px; }
</style>
</head>
<body>

  <section class="sheet envelope-wide" aria-label="Sobre horizontal">
    <div class="ring" style="left:6px; top:50px; width:164px; height:164px; border-width:16px;"><span class="ring-name" style="font-size:22px;">zelvo</span></div>
    <div class="ring" style="left:174px; top:48px; width:84px; height:84px; border-width:8px;"><span class="ring-name" style="font-size:11px;">zelvo</span></div>
    <div class="wordmark"><span class="name">zelvo</span><span class="tag">Promotions Group</span></div>
    <p class="address">Calle 18 No. 42 Ens. Mirador,<br>Santo Domingo<br>República Dominicana</p>
  </section>

  <section class="sheet envelope-tall" aria-label="Sobre vertical con ventana">
    <div class="wordmark"><span class="name">zelvo</span><span class="tag">Promotions Group</span></div>
    <p class="address">Calle 18 No. 42 Ens. Mirador,<br>Santo Domingo<br>República Dominicana</p>
    <div class="ring" style="left:150px; top:142px; width:124px; height:124px; border-width:12px;"><span class="ring-name" style="font-size:17px;">zelvo</span></div>
    <div class="ring" style="left:276px; top:296px; width:80px; height:80px; border-width:8px;"><span class="ring-name" style="font-size:11px;">zelvo</span></div>
    <div class="ring" style="left:358px; top:402px; width:66px; height:66px; border-width:7px;"><span class="ring-name" style="font-size:9px;">zelvo</span></div>
    <div class="window"></div>
  </section>

  <section class="sheet folder-red" aria-label="Carpeta roja">
    <div class="fold"></div>
    <span class="url">zelvo.com.do</span>
    <div class="wordmark"><span class="name">zelvo</span><span class="tag">Promotions Group</span></div>
    <p class="address">Calle 18 No. 42 Ens. Mirador,<br>Santo Domingo<br>República Dominicana</p>
  </section>

  <section class="sheet folder-white" aria-label="Carpeta blanca">
    <div class="fold"></div>
    <div class="hero"><span class="hero-dot"></span><span class="hero-name">zelvo</span></div>
    <p class="address">Calle 18 No. 42 Ens. Mirador,<br>Santo Domingo<br>República Dominicana</p>
    <div class="wordmark"><span class="name">zelvo</span><span class="tag">Promotions Group</span></div>
    <span class="url">zelvo.com.do</span>
  </section>

</body>
</html>
```